Modern business card design for professional copywriter

I'd like a business card design that I can use to have my cards printed out by quillprint.com as a squared corners business card (see artwork and design guidelines here: https://help.quillprint.com/hc/en-gb/sections/200570950-QUILL-Product-Templates)

The design should be clean and modern and reflect the colours, tone and branding on my website: https://tessavorrin.com.au

Target Market(s)

Professionals, B2B small business owners

Industry/Entity Type

Business

Contact Information for Business Card

Tessa Vorrin
m: 0468 905 327
e: tessa@tessavorrin.com.au
w: tessavorrin.com.au

Font styles to use
Sans Serif

Requirements
Must have
• Tagline: "Smart copywriting for clever business people"
• Brand colours: fd8000, 009984, 666666 and black
Nice to have

```html
<!DOCTYPE html>
<html lang="en">
<head>
<meta charset="utf-8">
<title>Tessa Vorrin – Business Card</title>
<link rel="stylesheet" href="https://fonts.googleapis.com/css2?family=Open+Sans:wght@400;600&display=swap">
<style>
  :root {
    --brand-orange: #fd8000;
    --brand-teal: #009984;
    --brand-grey: #666666;
    --card-teal: #14977f;
    --card-paper: #f1f0ee;
    --page-bg: #dcdcda;
    --text-light: #ffffff;
  }
  * { margin: 0; padding: 0; box-sizing: border-box; }
  html, body {
    width: 1200px;
    height: 900px;
    overflow: hidden;
    background: var(--page-bg);
    font-family: "Open Sans", Arial, sans-serif;
  }
  .business-card {
    position: absolute;
    left: 100px;
    top: 141px;
    width: 1000px;
    height: 618px;
    background: var(--card-paper);
    overflow: hidden;
    box-shadow: 0 14px 40px rgba(0, 0, 0, 0.18);
  }
  .card-artwork {
    position: absolute;
    inset: 0;
    width: 100%;
    height: 100%;
  }
  .teal-panel { fill: var(--card-teal); }
  .accent-edge {
    fill: none;
    stroke: var(--brand-orange);
    stroke-width: 10;
  }

  .holder-name {
    position: absolute;
    left: 37px;
    top: 48px;
    font-size: 36px;
    font-weight: 400;
    letter-spacing: 0.5px;
    color: var(--text-light);
  }
  .contact-list {
    position: absolute;
    left: 30px;
    top: 150px;
    list-style: none;
    color: var(--text-light);
    font-size: 23px;
    line-height: 34px;
  }
  .contact-item {
    display: flex;
    align-items: center;
    gap: 12px;
  }
  .contact-icon {
    width: 19px;
    height: 19px;
    flex: none;
    fill: var(--text-light);
  }
  .tagline {
    position: absolute;
    left: 47px;
    top: 477px;
    color: var(--text-light);
    font-size: 28px;
    line-height: 46px;
    letter-spacing: 0.8px;
    text-transform: uppercase;
  }
  .brand-lockup {
    position: absolute;
    left: 610px;
    top: 282px;
    display: flex;
    align-items: center;
    gap: 14px;
  }
  .brand-square {
    width: 26px;
    height: 26px;
    background: var(--brand-orange);
  }
  .brand-name {
    font-size: 46px;
    font-weight: 400;
    color: var(--brand-teal);
    letter-spacing: -0.3px;
  }
</style>
</head>
<body>
  <main class="business-card">
    <svg class="card-artwork" viewBox="0 0 1000 618" aria-hidden="true">
      <path class="teal-panel" d="M0 0 H470 C520 220 560 440 650 618 H0 Z"/>
      <path class="accent-edge" d="M475 -5 C525 220 565 440 655 623"/>
    </svg>

    <h1 class="holder-name">TESSA VORRIN</h1>

    <ul class="contact-list">
      <li class="contact-item">
        <svg class="contact-icon" viewBox="0 0 20 20" aria-hidden="true"><path d="M6 1h8a2 2 0 0 1 2 2v14a2 2 0 0 1-2 2H6a2 2 0 0 1-2-2V3a2 2 0 0 1 2-2zm0 3v11h8V4zm4 12.2a1 1 0 1 0 0 2 1 1 0 0 0 0-2z"/></svg>
        <span>0468 905 327</span>
      </li>
      <li class="contact-item">
        <svg class="contact-icon" viewBox="0 0 20 20" aria-hidden="true"><path d="M2 4h16v12H2zm1.5 1.5 6.5 5 6.5-5z"/></svg>
        <span>tessa@tessavorrin.com.au</span>
      </li>
      <li class="contact-item">
        <svg class="contact-icon" viewBox="0 0 20 20" aria-hidden="true"><path d="M10 1a9 9 0 1 0 0 18 9 9 0 0 0 0-18zm-1 3.5c1 .6 2.4.3 3 1.4.4.8-.8 1.5-1.6 1.7-1 .3-1.2 1.4-.4 2 1 .7 2.6.4 3 1.7.3 1-.6 2-.4 3 .1.6.6 1.1 1.1 1.3A7 7 0 0 1 4 6.5c1 .4 1.6 1.5 2.7 1.4C8 7.8 8 5.3 9 4.5z"/></svg>
        <span>tessavorrin.com.au</span>
      </li>
    </ul>

    <p class="tagline">Smart copywriting<br>for clever business people</p>

    <div class="brand-lockup">
      <span class="brand-square" aria-hidden="true"></span>
      <span class="brand-name">Tessa Vorrin</span>
    </div>
  </main>
</body>
</html>
```